A Modern & Sleek "Coming Soon" Page for an A.I Recruiting App

For the “Coming Soon” website, a simple background with no people in it. I've attached an A.I image of what the page should generally look like.

- A single mobile phone as the main focus where the user actually clicks on the, “notify me” button (after entering their email address).
- In the background where the pillars/columns are seen in the example, should be subtle pad locks that are in their opened position with a key inside the lock. I've attached images to try to illustrate this idea, but they are far away in style from what I'm looking for.

SLOGAN: Unlocking the power of meaningful connections
LOGO/TITLE: Should be the name as shown in image with only the name "KelvoLink" on it
COLORS: Purplish/blue hues. Should not be too feminine
NOTE: The user should only click once when signing up/entering their email.

Product: A recruiting platform that matches employers/employees with A.I. and prioritizing cultural fit/values system before skills. The industry we are tackling first is the caregiving industry (nannies, tutors, elderly). All users will be background screened and that info lives on the blockchain. All users will have the option to review and be reviewed/rated.

```html
<!DOCTYPE html>
<html lang="en">
<head>
<meta charset="UTF-8">
<title>KelvoLink – Coming Soon</title>
<link rel="stylesheet" href="https://fonts.googleapis.com/css2?family=Jost:ital,wght@0,300;0,400;1,400&display=swap">
<style>
  :root {
    --violet-deep: #3f08b8;
    --violet-mid: #4f17c8;
    --violet-soft: #6a3fd2;
    --violet-haze: #7b55d8;
    --screen: #4310bd;
    --phone-body: #17102a;
    --brand-rose: #c43a78;
    --white: #ffffff;
    --sage: #a9c3a2;
    --lilac: #b07cc0;
  }
  * { box-sizing: border-box; margin: 0; padding: 0; }
  html, body {
    width: 1200px;
    height: 662px;
    overflow: hidden;
    background: var(--violet-deep);
    font-family: "Jost", sans-serif;
  }
  .page {
    position: relative;
    width: 1200px;
    height: 662px;
    overflow: hidden;
    background: linear-gradient(180deg, var(--violet-haze) 0%, var(--violet-soft) 22%, var(--violet-mid) 48%, var(--violet-deep) 100%);
  }
  .heart-backdrop {
    position: absolute;
    inset: 0;
    background:
      radial-gradient(ellipse 340px 260px at 560px 330px, rgba(120, 70, 220, 0.45), transparent 70%),
      radial-gradient(ellipse 700px 220px at 600px 60px, rgba(150, 110, 230, 0.35), transparent 75%);
  }

  /* phone */
  .phone {
    position: absolute;
    left: 104px;
    top: 116px;
    width: 278px;
    height: 470px;
    border-radius: 34px;
    background: var(--phone-body);
    padding: 10px;
    transform: rotate(-4deg);
    box-shadow: 14px 18px 30px rgba(20, 0, 60, 0.45);
  }
  .phone-screen {
    position: relative;
    width: 100%;
    height: 100%;
    border-radius: 26px;
    background: var(--screen);
    overflow: hidden;
    text-align: left;
  }
  .phone-notch {
    position: absolute;
    left: 50%;
    top: 0;
    width: 120px;
    height: 22px;
    transform: translateX(-50%);
    background: var(--phone-body);
    border-radius: 0 0 14px 14px;
  }
  .phone-brand {
    position: absolute;
    left: 34px;
    top: 66px;
    font-weight: 300;
    font-size: 24px;
    letter-spacing: 2px;
    color: var(--brand-rose);
  }
  .phone-slogan {
    position: absolute;
    left: 68px;
    top: 174px;
    font-weight: 400;
    font-size: 21px;
    line-height: 26px;
    color: var(--white);
  }
  .notify-button {
    position: absolute;
    left: 92px;
    top: 346px;
    width: 140px;
    height: 48px;
    border: 2px solid var(--sage);
    border-radius: 24px;
    background: transparent;
    color: var(--white);
    font-family: "Jost", sans-serif;
    font-size: 17px;
    letter-spacing: 0.3px;
  }
  .phone-note {
    position: absolute;
    left: 108px;
    top: 406px;
    font-style: italic;
    font-size: 11px;
    line-height: 14px;
    color: var(--white);
  }

  /* lock */
  .lock-art {
    position: absolute;
    left: 472px;
    top: 232px;
    width: 242px;
    height: 376px;
    border-radius: 40px;
    background: linear-gradient(180deg, rgba(169, 195, 162, 0.55) 0%, rgba(176, 124, 192, 0.65) 55%, rgba(210, 200, 225, 0.45) 100%);
  }

  /* hero copy */
  .hero {
    position: absolute;
    left: 772px;
    top: 210px;
    color: var(--white);
  }
  .brand {
    font-weight: 300;
    font-size: 54px;
    letter-spacing: 4px;
    color: var(--brand-rose);
    line-height: 1;
  }
  .headline {
    margin-top: 34px;
    font-weight: 400;
    font-size: 51px;
    line-height: 58px;
    text-transform: uppercase;
    letter-spacing: 0.5px;
  }
  .signup-button {
    margin-top: 20px;
    width: 140px;
    height: 48px;
    border: 2px solid var(--sage);
    border-radius: 24px;
    background: transparent;
    color: var(--white);
    font-family: "Jost", sans-serif;
    font-size: 17px;
    letter-spacing: 0.3px;
  }
</style>
</head>
<body>
  <main class="page">
    <div class="heart-backdrop" role="img" aria-label="Soft backdrop of glossy violet hearts"></div>

    <div class="phone">
      <div class="phone-screen">
        <div class="phone-notch"></div>
        <p class="phone-brand">KelvoLink</p>
        <p class="phone-slogan">Unlocking<br>the power of<br>meaningful<br>connections</p>
        <button class="notify-button" type="button">NOTIFY ME</button>
        <p class="phone-note">Excepteur sint occaecat<br>cupidatat non</p>
      </div>
    </div>

    <div class="lock-art" role="img" aria-label="Illustration of an open padlock with a key in its keyhole"></div>

    <section class="hero">
      <h1 class="brand">KelvoLink</h1>
      <h2 class="headline">Unlocking<br>the power of<br>meaningful<br>connections</h2>
      <button class="signup-button" type="button">SIGN UP</button>
    </section>
  </main>
</body>
</html>
```